Spring Detox sale graphics for social media

You MUST read the Brief in the WORD document and follow the instructions there. I want to create 10 social media graphics (new Instagram size 4:5 (1080 x 1350 pixels) focusing on our Mother’s Day Spring Detox Sale graphics, using any of the pics attached. Use the attached pics, NO RANDOM STOCK PHOTOGRAPHY. For the color scheme of the graphics, they should all be complementary to the product colors or feel like Spring time.

Target Market(s)

primarily women

Requirements
Must have
• the photos and text attached

```html
<!DOCTYPE html>
<html lang="en">
<head>
<meta charset="utf-8">
<title>Spring Detox Sale – 25% Off All Supplements</title>
<link rel="stylesheet" href="https://fonts.googleapis.com/css2?family=Roboto:wght@900&family=Bebas+Neue&family=Lora:ital,wght@1,500&display=swap">
<style>
  :root {
    --page: #ffffff;
    --mint: #d2efe2;
    --leaf-tone: #c9a3b8;
    --swirl-tone: #9a9a9a;
    --pink-light: #fdd2e4;
    --pink-deep: #f59bb6;
    --ink-plum: #35294f;
    --magenta: #e8008a;
    --violet: #5e2a8e;
    --photo-tone-a: #e6e3e6;
    --photo-tone-b: #cdbdb6;
    --product-tone-a: #f4f4f4;
    --product-tone-b: #e2dfea;
  }
  html, body {
    margin: 0;
    width: 1200px;
    height: 1200px;
    overflow: hidden;
    background: var(--page);
  }
  .canvas {
    position: relative;
    width: 1200px;
    height: 1200px;
  }
  .sale-card {
    position: absolute;
    left: 240px;
    top: 150px;
    width: 720px;
    height: 900px;
    background: var(--mint);
    overflow: hidden;
  }
  .floral-band {
    position: absolute;
    left: 0;
    top: 0;
    width: 720px;
    height: 200px;
    background: linear-gradient(180deg, rgba(201,163,184,0.30), rgba(154,154,154,0.10) 70%, rgba(210,239,226,0));
  }
  .host-photo {
    position: absolute;
    left: 400px;
    top: 70px;
    width: 270px;
    height: 440px;
    border-radius: 18px;
    background: linear-gradient(180deg, var(--photo-tone-b) 0%, var(--photo-tone-a) 45%, var(--photo-tone-a) 100%);
  }
  .product-lineup {
    position: absolute;
    left: 345px;
    top: 480px;
    width: 345px;
    height: 130px;
    border-radius: 14px;
    background: linear-gradient(90deg, var(--product-tone-a), var(--product-tone-b), var(--product-tone-a));
  }
  .graphics {
    position: absolute;
    inset: 0;
  }
  .discount-text {
    font-family: "Roboto", Arial, sans-serif;
    font-weight: 900;
    fill: var(--ink-plum);
  }
  .headline {
    font-family: "Bebas Neue", Impact, sans-serif;
    fill: var(--magenta);
  }
  .tagline {
    font-family: "Lora", Georgia, serif;
    font-style: italic;
    font-weight: 500;
    fill: var(--violet);
  }
</style>
</head>
<body>
<main class="canvas">
  <section class="sale-card">
    <div class="floral-band" role="img" aria-label="Decorative pink leaves and grey swirling vines"></div>
    <div class="host-photo" role="img" aria-label="Photo of a smiling woman in a white cropped sweater pointing down at the supplements"></div>
    <div class="product-lineup" role="img" aria-label="Row of supplement bottles and cream tubes"></div>

    <svg class="graphics" width="720" height="900" viewBox="0 0 720 900">
      <defs>
        <linearGradient id="badgeFill" x1="0" y1="0" x2="1" y2="0">
          <stop offset="0" stop-color="var(--pink-light)"/>
          <stop offset="1" stop-color="var(--pink-deep)"/>
        </linearGradient>
        <clipPath id="shadowHalf">
          <rect x="200" y="0" width="400" height="900"/>
        </clipPath>
      </defs>

      <g class="discount-badge">
        <circle cx="200" cy="400" r="172" fill="var(--ink-plum)" clip-path="url(#shadowHalf)"/>
        <circle cx="200" cy="360" r="172" fill="url(#badgeFill)"/>
        <text class="discount-text" x="73" y="383" font-size="174" textLength="259" lengthAdjust="spacingAndGlyphs">25%</text>
        <text class="discount-text" x="107" y="484" font-size="121" textLength="189" lengthAdjust="spacingAndGlyphs">OFF</text>
      </g>

      <text class="headline" x="52" y="740" font-size="118" textLength="616" lengthAdjust="spacingAndGlyphs">ALL SUPPLEMENTS</text>
      <text class="tagline" x="88" y="826" font-size="68" textLength="560" lengthAdjust="spacingAndGlyphs">Spring Detox Sale!</text>
    </svg>
  </section>
</main>
</body>
</html>
```